Human Resource Consulting practice needs a business card design

We need a business card design (double sided colour) for our Human Resource (HR) consulting practice in regional New South Wales, australia. Our business name is Staff Compass. We support small and medium business across the Mid North Coast of New South Wales by providing them with outsourced HR support, services and products to help them achieve compliance with workplace legislation and across all areas of the employment lifecycle from recruitment to termination and everything in between. Our corporate colours are hot pink and black. The final design should communicate professionalism, trust, people focus.
I have attached the current (old) business card for your reference.

Target Market(s)

Business owners and high level managers

Industry/Entity Type

Business

Contact Information for Business Card

Name
Title
Phone no
Mobile no
Address
PO Box
email address
website

Colors
e34197

Requirements
Must have
• Tempate for changing business card personal details including Name, position title, mobile number, email address.
• Keep current logo and colours as per attached
• Logo must be presented in 2 colours or black only not white
Nice to have
• One side logo and graphic only other side logo and personal details
Should not have
• Should not be the same as the current version (attached) but a modern interpretation.
• Does not need a busy reverse side with our list of services as per current version. I feel this is too busy.
• No photos

```html
<!DOCTYPE html>
<html lang="en">
<head>
<meta charset="utf-8">
<title>Staff Compass – Business Card</title>
<link rel="stylesheet" href="https://fonts.googleapis.com/css2?family=Open+Sans:wght@400;600;700&display=swap">
<style>
  :root {
    --pink: #e34197;
    --charcoal: #333334;
    --ink: #3a3a3a;
    --paper: #ffffff;
    --backdrop: #e9e9ea;
    --rule: #9a9a9a;
  }
  html, body {
    margin: 0;
    padding: 0;
    width: 1200px;
    height: 900px;
    overflow: hidden;
    background: var(--backdrop);
    font-family: "Open Sans", Arial, sans-serif;
  }
  .canvas {
    position: relative;
    width: 1200px;
    height: 900px;
  }
  .card {
    position: absolute;
    left: 280px;
    width: 640px;
    height: 366px;
    border-radius: 34px;
    overflow: hidden;
    background: var(--paper);
    box-shadow: 0 6px 18px rgba(0,0,0,0.12);
  }
  .card--back { top: 64px; }
  .card--front { top: 470px; }
  .card__shapes {
    position: absolute;
    inset: 0;
    width: 100%;
    height: 100%;
  }
  .band { fill: var(--charcoal); }
  .swoosh { fill: var(--pink); }
  .web-path-text {
    fill: #ffffff;
    font-family: "Open Sans", Arial, sans-serif;
    font-size: 12px;
    font-weight: 600;
    letter-spacing: 2px;
  }

  .brand {
    position: absolute;
    display: flex;
    align-items: center;
    gap: 8px;
    color: var(--ink);
    font-weight: 600;
    line-height: 1;
    white-space: nowrap;
  }
  .brand__mark {
    width: 10px;
    height: 10px;
    background: var(--pink);
    align-self: flex-end;
    margin-bottom: 4px;
  }
  .card--back .brand { left: 300px; top: 78px; font-size: 38px; }
  .card--front .brand { left: 112px; top: 60px; font-size: 36px; }

  .contacts {
    position: absolute;
    left: 112px;
    top: 136px;
    margin: 0;
    padding: 0;
    list-style: none;
    font-size: 12.5px;
    color: var(--ink);
  }
  .contacts li {
    display: flex;
    align-items: center;
    gap: 8px;
    height: 20px;
  }
  .contacts svg {
    width: 12px;
    height: 12px;
    fill: var(--pink);
    flex: none;
  }

  .person {
    position: absolute;
    right: 56px;
    top: 196px;
    text-align: right;
  }
  .person__name {
    margin: 0;
    color: var(--pink);
    font-size: 20px;
    font-weight: 700;
    letter-spacing: 0.5px;
  }
  .person__rule {
    height: 2px;
    margin: 3px 0 4px;
    background: linear-gradient(to right, transparent, var(--rule) 30%, var(--rule));
  }
  .person__title {
    margin: 0;
    color: var(--ink);
    font-size: 16px;
    font-weight: 400;
  }
</style>
</head>
<body>
<main class="canvas">

  <section class="card card--back" aria-label="Card reverse">
    <svg class="card__shapes" viewBox="0 0 640 366" preserveAspectRatio="none" aria-hidden="true">
      <path class="band" d="M0,0 L70,0 C120,190 300,300 640,305 L640,366 L0,366 Z"/>
      <path class="swoosh" d="M150,200 C260,272 420,294 640,288 L640,298 C400,304 250,282 150,200 Z"/>
      <path id="web-line" d="M22,70 C80,210 220,300 420,326" fill="none"/>
      <text class="web-path-text"><textPath href="#web-line" startOffset="12%">www.staffcompass.au</textPath></text>
    </svg>
    <div class="brand"><span class="brand__name">Staff Compass</span><span class="brand__mark"></span></div>
  </section>

  <section class="card card--front" aria-label="Card front">
    <svg class="card__shapes" viewBox="0 0 640 366" preserveAspectRatio="none" aria-hidden="true">
      <path class="swoosh" d="M0,175 C60,262 180,312 320,322 C190,326 70,292 0,218 Z"/>
      <path class="band" d="M0,232 C90,322 250,345 390,332 C500,320 570,286 640,268 L640,366 L0,366 Z"/>
    </svg>

    <div class="brand"><span class="brand__name">Staff Compass</span><span class="brand__mark"></span></div>

    <ul class="contacts">
      <li><svg viewBox="0 0 12 12"><path d="M3 0h6a1 1 0 0 1 1 1v10a1 1 0 0 1-1 1H3a1 1 0 0 1-1-1V1a1 1 0 0 1 1-1zm0 1.5v8h6v-8z"/></svg>0412 555 019</li>
      <li><svg viewBox="0 0 12 12"><path d="M2.5 0.5l2 2.5-1.2 1.4c.7 1.6 2 2.9 3.6 3.6L8.3 6.8l2.5 2L9.5 11C5 10.6 1.4 7 1 2.5z"/></svg>02 6555 0142</li>
      <li><svg viewBox="0 0 12 12"><path d="M0 2h12v8H0zm1 1v.3l5 3.2 5-3.2V3z"/></svg>daniel@staffcompass.au</li>
      <li><svg viewBox="0 0 12 12"><circle cx="6" cy="6" r="5.5"/><path d="M0.5 6h11M6 0.5c-2 2-2 9 0 11M6 0.5c2 2 2 9 0 11" stroke="#fff" stroke-width="0.8" fill="none"/></svg>www.staffcompass.au</li>
      <li><svg viewBox="0 0 12 12"><path d="M6 0a4 4 0 0 1 4 4c0 3-4 8-4 8S2 7 2 4a4 4 0 0 1 4-4zm0 2.5a1.5 1.5 0 1 0 0 3 1.5 1.5 0 0 0 0-3z"/></svg>Level 2, 14 Harbour Street, Port Macquarie</li>
    </ul>

    <div class="person">
      <p class="person__name">DANIEL HARTLEY</p>
      <div class="person__rule"></div>
      <p class="person__title">Managing Director</p>
    </div>
  </section>

</main>
</body>
</html>
```